Webshop for furniture and lamps

We need a design for a web shop with APP that should have two options:
1-Webshop in general which should attract to private customer in general and
2-Website that is meant to attract big customers as hotels and restaurants who would have their own customerize login.

That's the idea behind the shop.

It should be diveded into 4 parts
vintage furniture
rattan set outdoor and indoor
lamps and
wooden wall decor

The name of the shop is loma vereda!

Please kindly make me an offer.

Reason: Dear designers, so far there hasn't been a design that really matched. Look up German web sites like www.glimmerhof-wohnen.de or www.sitzraum77.de... Haven't been convinced by designs! Sorry folks. Please submit some new ones. Kind regards Ned

```html
<!DOCTYPE html>
<html lang="en">
<head>
<meta charset="utf-8">
<title>Loma Vereda – Furniture &amp; Lamp</title>
<link rel="stylesheet" href="https://fonts.googleapis.com/css2?family=Roboto:wght@300;400;500&family=Roboto+Slab:wght@300&display=swap">
<style>
:root{
  --coral:#f25a4e;
  --coral-soft:#e86a5f;
  --ink:#1d1f21;
  --bar:#2a2d30;
  --side:#26292c;
  --line:#4a4e52;
  --black:#050505;
  --white:#ffffff;
  --muted:#c9c9c9;
  --panel:rgba(110,110,110,.82);
}
*{margin:0;padding:0;box-sizing:border-box}
html,body{width:1200px;height:794px;overflow:hidden;background:var(--ink)}
body{position:relative;font-family:'Roboto',Arial,sans-serif;color:var(--white)}
.abs{position:absolute}

/* brand + header */
.brand{left:0;top:0;width:260px;height:65px;background:var(--coral);display:flex;align-items:center;justify-content:center;font-family:'Roboto Slab',Georgia,serif;font-weight:300;font-size:28px}
.topbar{left:260px;top:0;width:940px;height:65px;background:linear-gradient(#2e3134,#0f1011)}
.search{left:659px;top:15px;width:189px;height:29px;border-radius:3px;background:#4a4d50;display:flex;align-items:center;padding-left:14px;font-size:13px;color:#e6e6e6}
.search-btn{left:818px;top:15px;width:30px;height:29px;background:var(--coral);border-radius:0 3px 3px 0}
.cart{left:876px;top:20px;display:flex;align-items:center;gap:8px;font-size:12px;font-weight:500}
.account{left:976px;top:23px;font-size:13px;color:#dcdcdc}
.account span{color:#9a9a9a;margin:0 4px}

/* sidebar */
.sidebar{left:0;top:65px;width:260px;height:386px;background:linear-gradient(#2b2e31,#1a1c1e)}
.menu{left:0;top:115px;width:260px;list-style:none}
.menu li{height:40.5px;border-top:1px solid var(--line);display:flex;align-items:center;padding-left:55px;font-size:14px;background:linear-gradient(#2a2d30,#1f2124)}
.menu li:nth-child(n+7){padding-left:51px;background:linear-gradient(#191b1d,#101112)}
.menu li:last-child{border-bottom:1px solid var(--line)}
.menu .active{color:var(--coral)}
.feature{left:0;top:451px;width:260px;height:192px;background:var(--white);color:#222;text-align:center}
.feature-title{margin-top:14px;font-size:14px}
.feature-photo{left:60px;top:45px;width:132px;height:96px;border-radius:10px;background:radial-gradient(ellipse at 50% 30%,#8c8e90,#4b4c4e 70%,#fff 72%)}
.feature-next{left:224px;top:76px}
.btn-small{left:82px;top:151px;width:90px;height:29px;background:var(--coral-soft);border-radius:3px;color:var(--white);font-size:13px;display:flex;align-items:center;justify-content:center;box-shadow:0 2px 0 #b5473e}
.side-foot{left:0;top:643px;width:260px;height:151px;background:var(--black)}
.social{left:68px;top:676px;display:flex;gap:11px}
.social span{width:41px;height:41px;border-radius:50%;background:var(--white);border:2px dashed var(--black);outline:2px solid var(--white);color:#111;font-size:10px;font-weight:500;display:flex;align-items:center;justify-content:center}
.cards{left:54px;top:747px;display:flex;gap:10px}
.cards span{width:51px;height:30px;background:#dfe3e8;color:#1d3f7a;font-size:10px;font-weight:500;display:flex;align-items:center;justify-content:center}

/* hero */
.hero{left:260px;top:65px;width:940px;height:673px;background:linear-gradient(90deg,#6f6c6f 0%,#8d8a8c 16%,#5f5a58 30%,#8e6d53 45%,#a98566 65%,#8a6a52 85%,#6f5646 100%)}
.hero-bed{left:760px;top:470px;width:440px;height:90px;background:linear-gradient(#e9e3da,#cfc5b8)}
.hero-title{left:616px;top:212px;font-size:43px;line-height:1.1;text-shadow:0 3px 4px rgba(0,0,0,.6)}
.hero-title .big{font-size:50px;display:block;margin-top:10px}
.btn-hero{left:613px;top:341px;width:161px;height:50px;background:#141516;border-radius:5px;font-size:23px;display:flex;align-items:center;justify-content:center;box-shadow:0 3px 6px rgba(0,0,0,.5)}
.slide-next{left:1155px;top:256px;width:96px;height:96px;border-radius:50%;background:rgba(20,20,20,.85)}
.slide-next svg{position:absolute;left:24px;top:36px}

/* services */
.strip{left:260px;top:551px;width:620px;height:45px;background:rgba(30,30,30,.78)}
.tag{height:45px;background:var(--coral-soft);font-size:20px;display:flex;align-items:center;padding-left:19px}
.services-tag{left:260px;top:551px;width:154px}
.tiles{left:260px;top:596px;display:flex;gap:1px}
.tile{position:relative;width:154px;height:142px}
.tile .photo{position:absolute;inset:0}
.tile .label{position:absolute;left:0;bottom:0;width:100%;height:33px;background:rgba(60,60,60,.8);font-size:12px;display:flex;align-items:center;padding-left:9px}
.t1 .photo{background:linear-gradient(135deg,#a58a6c,#c9574a 45%,#5d7c8c)}
.t2 .photo{background:linear-gradient(#7a7466,#2d2f31 60%,#1a1a1a)}
.t3 .photo{background:linear-gradient(#ffffff,#ffffff 20%,#e14a22 40%,#ffffff 55%)}
.t4 .photo{background:linear-gradient(#efe9df,#6e4a32 30%,#4a3020 80%)}

/* news */
.news-head{left:880px;top:551px;width:320px;height:45px;background:rgba(35,35,35,.8)}
.news-tag{left:880px;top:551px;width:119px;padding-left:27px}
.news-next{left:1128px;top:561px}
.news{left:880px;top:596px;width:320px;height:142px;background:var(--panel);padding:14px 18px 0 18px}
.news-date{font-size:15px;font-weight:300}
.news-text{margin-top:9px;padding-left:4px;font-size:14px;line-height:22px;font-weight:300}
.news-more{padding-left:4px;margin-top:4px;font-size:12px;font-style:italic;color:var(--coral)}

/* footer */
.footer{left:260px;top:738px;width:940px;height:56px;background:#1a1a1a}
.footer-links{left:275px;top:762px;font-size:13px}
.footer-links span{margin:0 7px}
.copyright{left:993px;top:761px;font-size:13px}
</style>
</head>
<body>
<div class="abs brand">Loma Vereda</div>
<div class="abs topbar"></div>
<div class="abs search">Search</div>
<div class="abs search-btn">
  <svg width="30" height="29" viewBox="0 0 30 29"><circle cx="13" cy="12.5" r="5.5" fill="none" stroke="#fff" stroke-width="2"/><line x1="17" y1="16.5" x2="22" y2="21.5" stroke="#fff" stroke-width="2.5"/></svg>
</div>
<div class="abs cart">
  <svg width="21" height="18" viewBox="0 0 21 18"><path d="M1 2h3l3 10h10l2-7H6" fill="none" stroke="#ddd" stroke-width="1.5"/><circle cx="8" cy="15.5" r="1.5" fill="#ddd"/><circle cx="16" cy="15.5" r="1.5" fill="#ddd"/></svg>
  Cart : 0
</div>
<div class="abs account">Log in<span>or</span>Create an account</div>

<div class="abs sidebar"></div>
<ul class="abs menu">
  <li class="active">HOME</li><li>ABOUT US</li><li>SERVICES</li><li>PRODUCTS</li><li>CUSTOMERS</li><li>BLOG</li><li>NEWS</li><li>CONTACT US</li>
</ul>

<div class="abs feature">
  <p class="feature-title">Ipsum is simply dummy</p>
  <div class="abs feature-photo" role="img" aria-label="Round grey rattan table with tucked-in chairs"></div>
  <svg class="abs feature-next" width="16" height="28" viewBox="0 0 16 28"><path d="M2 2l12 12L2 26" fill="none" stroke="#333" stroke-width="2"/></svg>
  <div class="abs btn-small">BUY NOW</div>
</div>
<div class="abs side-foot"></div>
<div class="abs social"><span>Folkring</span><span>Pixlane</span><span>Chirpit</span></div>
<div class="abs cards"><span>Paynor</span><span>Cardwell</span><span>Tallycard</span></div>

<div class="abs hero" role="img" aria-label="Modern bedroom with wood block wall, grey wardrobe and white bed"></div>
<div class="abs hero-bed"></div>
<h1 class="abs hero-title" style="font-weight:400">LOMA VEREDA<span class="big">FURNITURE &amp; LAMP</span></h1>
<div class="abs btn-hero">BUY NOW</div>
<div class="abs slide-next"><svg width="12" height="26" viewBox="0 0 12 26"><path d="M1 1l10 12L1 25z" fill="#fff"/></svg></div>

<div class="abs strip"></div>
<div class="abs tag services-tag">SERVICES</div>
<div class="abs tiles">
  <div class="tile t1"><div class="photo" role="img" aria-label="Painted vintage wooden table"></div><div class="label">VINTAGE FURNITURE</div></div>
  <div class="tile t2"><div class="photo" role="img" aria-label="Black rattan outdoor dining set"></div><div class="label">RATTAN SET OUTDOOR</div></div>
  <div class="tile t3"><div class="photo" role="img" aria-label="Floor lamp with orange shade"></div><div class="label">LAMPS</div></div>
  <div class="tile t4"><div class="photo" role="img" aria-label="Wooden wall cabinet with painted tiles"></div><div class="label">WOODEN WALL DECOR</div></div>
</div>

<div class="abs news-head"></div>
<div class="abs tag news-tag">NEWS</div>
<svg class="abs news-next" width="16" height="28" viewBox="0 0 16 28"><path d="M2 2l12 12L2 26" fill="none" stroke="#fff" stroke-width="2"/></svg>
<div class="abs news">
  <p class="news-date">28 /JULY /2014</p>
  <p class="news-text">Lorem Ipsum is simply dummy text of the printing and typesetting industry. Lorem Ipsum has been the industry's</p>
  <p class="news-more">Read More</p>
</div>

<div class="abs footer"></div>
<div class="abs footer-links">ABOUT US<span>|</span>SEARCH<span>|</span>CONTACT US</div>
<div class="abs copyright">Copyright © Loma Vereda</div>
</body>
</html>
```